Business Card Design for company

We want new business cards. We'd like something different-- yet still highly professional. Our tagline is Providing leadership, delivering success. Stock photos are ok, as long as they are relevant and look upscale.

Target Market(s)

Architecture/Business Management Consulting/Engineering Consulting

Contact Information for Business Card

dark gray background with pops of blue might be good, but you tell me. You're the designers. Rounded corners might be nice, but again, you tell me.

Font styles to use
Serif
Sans Serif

Colors
3276b5
5c5c5c
9d9d9d
fbfbfb

Requirements
Nice to have
• Something different, but still very professional.

```html
<!DOCTYPE html>
<html lang="en">
<head>
<meta charset="utf-8">
<title>Veltra Partners business cards</title>
<link href="https://fonts.googleapis.com/css2?family=Open+Sans:wght@400;600;700&display=swap" rel="stylesheet">
<style>
  :root {
    --blue: #3276b5;
    --blue-deep: #285f95;
    --charcoal: #45484d;
    --gray-dark: #5c5c5c;
    --gray-light: #9d9d9d;
    --paper: #fbfbfb;
    --backdrop: #1f2022;
    --back-top: #72767d;
    --back-bottom: #3d3f44;
  }
  * { margin: 0; padding: 0; box-sizing: border-box; }
  html, body {
    width: 1200px;
    height: 885px;
    overflow: hidden;
    background: var(--backdrop);
    font-family: "Open Sans", Arial, sans-serif;
  }
  .canvas {
    position: relative;
    width: 1200px;
    height: 885px;
  }
  .card {
    position: absolute;
    width: 640px;
    height: 366px;
    border-radius: 6px;
    overflow: hidden;
    box-shadow: 0 18px 40px rgba(0,0,0,0.55);
  }

  /* Back of card */
  .card-back {
    left: 70px;
    top: 60px;
    background: linear-gradient(160deg, var(--back-top) 0%, var(--back-bottom) 75%);
  }
  .card-back .brand-name {
    position: absolute;
    left: 0;
    right: 0;
    top: 122px;
    text-align: center;
    font-weight: 700;
    font-size: 64px;
    letter-spacing: 4px;
    color: var(--blue);
  }
  .card-back .tagline {
    position: absolute;
    left: 0;
    right: 0;
    bottom: 40px;
    text-align: center;
    font-size: 15px;
    color: var(--paper);
    letter-spacing: 0.3px;
  }
  .tagline .dot {
    display: inline-block;
    width: 6px;
    height: 6px;
    border-radius: 50%;
    background: var(--paper);
    margin: 0 10px;
    vertical-align: middle;
  }

  /* Front of card */
  .card-front {
    left: 490px;
    top: 459px;
    background: var(--paper);
  }
  .card-front .shapes {
    position: absolute;
    inset: 0;
  }
  .card-front .brand-name {
    position: absolute;
    left: 330px;
    top: 78px;
    width: 290px;
    text-align: center;
    font-weight: 700;
    font-size: 46px;
    line-height: 1.05;
    letter-spacing: 2px;
    color: var(--blue);
  }
  .identity {
    position: absolute;
    left: 44px;
    top: 72px;
    color: var(--paper);
  }
  .identity .person {
    font-weight: 700;
    font-size: 21px;
    letter-spacing: 0.5px;
    line-height: 1.1;
  }
  .identity .role {
    font-size: 14px;
    letter-spacing: 0.6px;
    margin-bottom: 6px;
  }
  .identity .address {
    font-size: 14px;
    line-height: 1.35;
  }
  .contacts {
    position: absolute;
    left: 44px;
    bottom: 28px;
    list-style: none;
    color: var(--paper);
    font-size: 14px;
    line-height: 1.5;
  }
  .contacts li {
    display: flex;
    align-items: center;
    gap: 10px;
  }
  .contacts svg {
    width: 14px;
    height: 14px;
    flex: none;
  }
</style>
</head>
<body>
<main class="canvas">

  <section class="card card-back" aria-label="Card back">
    <div class="brand-name">VELTRA</div>
    <p class="tagline">Providing leadership<span class="dot"></span>delivering success</p>
  </section>

  <section class="card card-front" aria-label="Card front">
    <svg class="shapes" viewBox="0 0 640 366" preserveAspectRatio="none" aria-hidden="true">
      <polygon points="0,0 300,0 222,190 0,236" fill="var(--blue-deep)"/>
      <polygon points="0,244 224,198 640,264 640,366 0,366" fill="var(--charcoal)"/>
    </svg>

    <div class="brand-name">VELTRA<br>PARTNERS</div>

    <div class="identity">
      <p class="person">MARCUS HALE</p>
      <p class="role">PRESIDENT</p>
      <p class="address">4120 Alder Crest Road<br>Lakeview, NY 10950</p>
    </div>

    <ul class="contacts">
      <li>
        <svg viewBox="0 0 16 16" aria-hidden="true"><path d="M2 5c0-2 3-3 6-3s6 1 6 3v1h-3V5H5v1H2z M4 7h8l2 6H2z" fill="currentColor"/><circle cx="8" cy="10.5" r="1.6" fill="var(--charcoal)"/></svg>
        555 0142 2290
      </li>
      <li>
        <svg viewBox="0 0 16 16" aria-hidden="true"><rect x="4" y="1" width="8" height="14" rx="1.5" fill="none" stroke="currentColor" stroke-width="1.6"/><circle cx="8" cy="12.5" r="0.9" fill="currentColor"/></svg>
        555 0187 4416
      </li>
      <li>
        <svg viewBox="0 0 16 16" aria-hidden="true"><rect x="1" y="3" width="14" height="10" fill="currentColor"/><path d="M1 3l7 6 7-6" fill="none" stroke="var(--charcoal)" stroke-width="1.3"/></svg>
        marcus@veltrapartners.com
      </li>
      <li>
        <svg viewBox="0 0 16 16" aria-hidden="true"><circle cx="8" cy="8" r="7" fill="currentColor"/><path d="M1 8h14M8 1c-3 3-3 11 0 14M8 1c3 3 3 11 0 14" fill="none" stroke="var(--charcoal)" stroke-width="1"/></svg>
        www.veltrapartners.com
      </li>
    </ul>
  </section>

</main>
</body>
</html>
```